Residential Remodeling Contractor needs updated business card

I need a new design for my business card.
Name of the company is Ridgefell Construction. I need a card that commands presence, strength, integrity. I have been in business for 28 years. I am a Residential Remodeling Contractor that covers all aspects of a residential remodel and build.

```html
<!DOCTYPE html>
<html lang="en">
<head>
<meta charset="utf-8">
<title>Ridgefell Construction – Business Card</title>
<link rel="stylesheet" href="https://fonts.googleapis.com/css2?family=Open+Sans:wght@400;600;700&display=swap">
<style>
  :root {
    --stage: #222222;
    --card-blue: #213e7c;
    --ink-white: #ffffff;
    --rule: rgba(255,255,255,0.55);
  }
  * { box-sizing: border-box; margin: 0; padding: 0; }
  html, body { width: 1200px; height: 780px; overflow: hidden; }
  body {
    background: var(--stage);
    font-family: "Open Sans", Arial, sans-serif;
    color: var(--ink-white);
    display: flex;
    align-items: center;
    justify-content: center;
    gap: 50px;
  }
  .card {
    position: relative;
    width: 540px;
    height: 309px;
    background: var(--card-blue);
    overflow: hidden;
  }

  /* Back: contact side */
  .card-back .brand {
    position: absolute;
    left: 34px;
    top: 44px;
    width: 220px;
    font-weight: 600;
    font-size: 26px;
    line-height: 1.15;
    letter-spacing: 0.5px;
  }
  .card-back .divider {
    position: absolute;
    left: 268px;
    top: 42px;
    width: 1px;
    height: 178px;
    background: var(--rule);
  }
  .card-back .contact {
    position: absolute;
    left: 292px;
    top: 58px;
  }
  .person-name {
    font-weight: 700;
    font-size: 29px;
    line-height: 1.05;
  }
  .person-title {
    font-size: 14px;
    margin-top: 2px;
  }
  .contact-list {
    list-style: none;
    margin-top: 18px;
    font-size: 14px;
    line-height: 1.55;
  }
  .contact-list li { display: flex; align-items: center; gap: 7px; }
  .contact-list svg { width: 12px; height: 12px; flex: none; }
  .address-band {
    position: absolute;
    left: 0;
    right: 0;
    bottom: 0;
    height: 40px;
    background: var(--ink-white);
    color: var(--card-blue);
    font-size: 15px;
    display: flex;
    align-items: center;
    justify-content: center;
    letter-spacing: 0.2px;
  }

  /* Front: brand side */
  .card-front {
    display: flex;
    align-items: center;
    justify-content: center;
  }
  .card-front .brand {
    font-weight: 600;
    font-size: 46px;
    line-height: 1.1;
    text-align: center;
    letter-spacing: 1px;
  }
</style>
</head>
<body>

<section class="card card-back" aria-label="Business card, contact side">
  <div class="brand">Ridgefell Construction</div>
  <div class="divider"></div>
  <div class="contact">
    <div class="person-name">Daniel Orvis</div>
    <div class="person-title">Managing Director</div>
    <ul class="contact-list">
      <li>
        <svg viewBox="0 0 12 12" aria-hidden="true"><path fill="#fff" d="M2.4 0.8l1.8 0.2 0.6 2.3-1.2 0.9c0.6 1.3 1.6 2.3 2.9 2.9l0.9-1.2 2.3 0.6 0.2 1.8c0 0.6-0.5 1-1.1 1C4.4 9.1 2.9 7.6 1.4 1.9c0-0.6 0.4-1.1 1-1.1z"/></svg>
        (555) 214-0387
      </li>
      <li>
        <svg viewBox="0 0 12 12" aria-hidden="true"><rect x="0.8" y="2.5" width="10.4" height="7" fill="none" stroke="#fff" stroke-width="1.2"/><path d="M1 3l5 3.6L11 3" fill="none" stroke="#fff" stroke-width="1.2"/></svg>
        info@ridgefellbuild.com
      </li>
      <li>
        <svg viewBox="0 0 12 12" aria-hidden="true"><circle cx="6" cy="6" r="5" fill="none" stroke="#fff" stroke-width="1.1"/><ellipse cx="6" cy="6" rx="2.2" ry="5" fill="none" stroke="#fff" stroke-width="1"/><path d="M1 6h10" stroke="#fff" stroke-width="1"/></svg>
        www.ridgefellbuild.com
      </li>
    </ul>
  </div>
  <div class="address-band">4180 Meadow Crest Ln. Suite 120 Granbury, TX 76048</div>
</section>

<section class="card card-front" aria-label="Business card, brand side">
  <div class="brand">Ridgefell<br>Construction</div>
</section>

</body>
</html>
```